Business card for Crestline Bathrooms

Please design a business card for our bathroom renovation business. You can use my existing logo, but if you have an idea to modernize it, I would like to see it. Please see attached files first. I would like to use the blue and the orange theme. I like the concept of using the shower head in the logo. Please find following a design (or two) that I have been trying to create with my limited resources. That design was for a sign, but I was going to adopt it and use it as a business card as well. I like the concept of the water splash but I don’t think it “flows” nicely together with the logo. Another thought is that maybe creating the logo out of water splash could work and have a dramatic effect (like the water text and the butterfly picture attached with similar background instead of white). If the above doesn’t work I would like to see a modern simplified design. One of the attached files named as the unwanted business card has all the details that I want included in the business card. Please note that it is two sided.
Updates

I am very thankful for the designs that I have received, but they are very similar and only a couple of attempts to do something with the water splash as per my original brief. Modernizing the logo and having it made out of out of water splash with the orange as color accent could work and have a dramatic effect (like the water text and the butterfly picture attached with similar background instead of white). Please do not use the butterfly itself! This is just an example that images can be created out of water splash.

Contact Information for Business Card

all the details are on the unwonted business card file included

Colors
3176b5

Requirements
Nice to have
• Copied from the brief:
• ... maybe creating the logo out of water splash could work and have a dramatic effect (like the water text and the butterfly picture attached with similar background instead of white). Please do not use the butterfly itself!
Should not have
• I am getting designs with a butterfly. The butterfly picture was an example of creating something from a water splash. The butterfly itself has no association with anything other than the concept of creating a logo out of water splash. Sorry, I thought I was clear in the brief.

```html
<!DOCTYPE html>
<html lang="en">
<head>
<meta charset="utf-8">
<title>Crestline Bathrooms – Business Card</title>
<link href="https://fonts.googleapis.com/css2?family=Roboto:wght@400;500&family=Short+Stack&display=swap" rel="stylesheet">
<style>
  :root {
    --page-bg: #e3e3e3;
    --navy: #1a3152;
    --navy-deep: #12233c;
    --splash-light: #8fa6bf;
    --coral: #e8705f;
    --white: #ffffff;
    --card-white: #f4f4f4;
    --body-grey: #555555;
    --badge-grey: #6a6a6a;
  }
  html, body {
    margin: 0;
    padding: 0;
    width: 1200px;
    height: 960px;
    overflow: hidden;
    background: var(--page-bg);
  }
  .canvas {
    position: relative;
    width: 1200px;
    height: 960px;
  }
  .card {
    position: absolute;
    width: 600px;
    height: 343px;
    overflow: hidden;
  }
  /* Front side */
  .card-front {
    left: 314px;
    top: 113px;
    background: var(--navy);
  }
  .splash-visual {
    position: absolute;
    left: 0;
    top: 0;
    width: 290px;
    height: 343px;
    background:
      radial-gradient(ellipse 160px 90px at 110px 300px, rgba(220,232,244,0.75), rgba(220,232,244,0) 70%),
      radial-gradient(ellipse 60px 140px at 30px 240px, rgba(190,208,228,0.55), rgba(190,208,228,0) 75%),
      linear-gradient(90deg, #2c4f7a 0%, #23426a 50%, var(--navy) 100%);
  }
  .contact {
    position: absolute;
    left: 307px;
    top: 86px;
    color: var(--white);
    font-family: "Roboto", sans-serif;
    font-size: 15px;
    line-height: 19px;
  }
  .contact-name {
    margin: 0 0 12px;
    font-family: "Short Stack", cursive;
    font-weight: 400;
    font-size: 24px;
    line-height: 30px;
    color: var(--coral);
  }
  .contact-address {
    margin: 0 0 10px;
    font-style: normal;
  }
  .contact-list {
    list-style: none;
    margin: 0;
    padding: 0;
  }
  .contact-list li {
    display: flex;
    align-items: center;
    gap: 8px;
  }
  .contact-icon {
    width: 14px;
    height: 14px;
    flex: none;
    fill: var(--coral);
  }
  /* Back side */
  .card-back {
    left: 311px;
    top: 472px;
    background: var(--card-white);
    text-align: center;
    font-family: "Roboto", sans-serif;
  }
  .brand {
    position: absolute;
    left: 0;
    right: 0;
    top: 112px;
    display: flex;
    justify-content: center;
    align-items: center;
    gap: 10px;
  }
  .brand-dot {
    width: 14px;
    height: 14px;
    border-radius: 50%;
    background: var(--coral);
  }
  .brand-name {
    font-size: 28px;
    font-weight: 500;
    color: var(--navy);
    letter-spacing: 0.5px;
  }
  .services {
    position: absolute;
    left: 0;
    right: 0;
    top: 188px;
    margin: 0;
    padding: 0;
    list-style: none;
    color: var(--body-grey);
    font-size: 14.5px;
    line-height: 18px;
  }
  .memberships {
    position: absolute;
    left: 190px;
    top: 276px;
    display: flex;
    align-items: center;
    gap: 18px;
  }
  .badge-round {
    width: 32px;
    height: 34px;
    border-radius: 8px;
    background: var(--badge-grey);
  }
  .badge-divider {
    width: 1px;
    height: 34px;
    background: var(--badge-grey);
  }
  .badge-wide {
    width: 118px;
    height: 26px;
    border-radius: 3px;
    background: var(--badge-grey);
  }
</style>
</head>
<body>
<main class="canvas">
  <section class="card card-front" aria-label="Card front">
    <div class="splash-visual" role="img" aria-label="Photograph of a water splash with droplets against dark blue"></div>
    <div class="contact">
      <h1 class="contact-name">Daniel Marsh</h1>
      <address class="contact-address">PO Box 48<br>Harwood Vale 2731</address>
      <ul class="contact-list">
        <li>
          <svg class="contact-icon" viewBox="0 0 24 24" aria-hidden="true"><path d="M6.6 10.8a15.1 15.1 0 0 0 6.6 6.6l2.2-2.2c.3-.3.7-.4 1-.2 1.1.4 2.3.6 3.6.6.6 0 1 .4 1 1V20c0 .6-.4 1-1 1A17 17 0 0 1 3 4c0-.6.4-1 1-1h3.5c.6 0 1 .4 1 1 0 1.3.2 2.5.6 3.6.1.3 0 .7-.2 1z"/></svg>
          0400 555 218
        </li>
        <li>
          <svg class="contact-icon" viewBox="0 0 24 24" aria-hidden="true"><path d="M7 1h10a2 2 0 0 1 2 2v18a2 2 0 0 1-2 2H7a2 2 0 0 1-2-2V3a2 2 0 0 1 2-2zm0 3v14h10V4zm5 15.5a1.2 1.2 0 1 0 0 2.4 1.2 1.2 0 0 0 0-2.4z"/></svg>
          5550 1942
        </li>
        <li>
          <svg class="contact-icon" viewBox="0 0 24 24" aria-hidden="true"><path d="M2 5h20v14H2zm2 2v.5l8 5 8-5V7l-8 5z"/></svg>
          daniel@crestlinebathrooms.com.au
        </li>
        <li>
          <svg class="contact-icon" viewBox="0 0 24 24" aria-hidden="true"><path d="M12 2a10 10 0 1 0 0 20 10 10 0 0 0 0-20zm-1 17.9A8 8 0 0 1 4.2 10.2L9 15v1a2 2 0 0 0 2 2zm6.9-2.5A2 2 0 0 0 16 16h-1v-3a1 1 0 0 0-1-1H8v-2h2a1 1 0 0 0 1-1V7h2a2 2 0 0 0 2-2v-.4a8 8 0 0 1 2.9 12.8z"/></svg>
          crestlinebathrooms.com.au
        </li>
      </ul>
    </div>
  </section>

  <section class="card card-back" aria-label="Card back">
    <div class="brand">
      <span class="brand-dot" aria-hidden="true"></span>
      <span class="brand-name">Crestline Bathrooms</span>
    </div>
    <ul class="services">
      <li>Complete Bathroom Renovations &amp; Remodelling</li>
      <li>Highly Skilled &amp; Qualified Tradespeople</li>
      <li>Professional Service From Concept To Completion</li>
      <li>All Work Guaranteed</li>
    </ul>
    <div class="memberships">
      <div class="badge-round" role="img" aria-label="Industry association membership badge"></div>
      <div class="badge-divider" aria-hidden="true"></div>
      <div class="badge-wide" role="img" aria-label="Builders association membership badge"></div>
    </div>
  </section>
</main>
</body>
</html>
```